Counseling Practice Business Card

I need a professional looking business card incorporating my new logo that was just completed. Card needs to incorporate my name and title, description of my specialty, my address, my phone number, my fax number, my email and my website URL. I need to be able to choose design on/with different paper colors and textures.
I do not have a lot of business card ideas so I am open to anything but I want bold,sharp, clear card without additional designs other than my logo (see attached file info). I am open to different color backgrounds or paper colors including black. I do not like traditional brackets around area codes in phone number or dashes between numbers in phone number. Am open to other ways of presenting including periods between numbers as appropriate. I do not know enough to know what I like yet but I want card to coordinate and work together with my logo. My practice emphasizes natural mental health interventions so any use of color (with background paper color or the blue and green in my logo) that elicits nature is nice. In addition to black, any natural brown or wood looking background might be desirable also. Most of the offerings so far look very similar and boring.

Target Market(s)

Potential therapy clients and other professionals

Contact Information for Business Card

Card information:
Gerald M. Whitcombe, Ph.D.
Licensed Clinical Psychologist
Integrative Health Coach
4812 Marlowe Ridge Blvd SE
Suite 310
Duluth, GA 30096
(770) 415-2983 phone
(770) 581-4096 fax
drgeraldwhitcombe@quillmarsh.net
brightfernwellness.net

Font styles to use
Serif
Sans Serif
Other font styles liked:
• anything that you think looks crisp, clear and easily readable

Requirements
Must have
• Any color used should coordinate with my logo design (see attached files).
• Card should be printed horizontally so top and bottom are longest sides of rectangle.
• Background color or paper color should complement and highlight logo. Do not like a white background. black, grey, brown or any color my logo would blend well with.
Nice to have
• I would like designer to utilize color to highlight letters/name or phone-fax-web symbols.
• Bottom edge of card could be highlighted if appropriate to an idea.
Should not have
• I would NOT want the card to have a pure white background at all.
• No clear cards.
• Cards should be oriented with long sides on bottom and top, NOT sides. DO NOT LIKE THIS THIN TALL ORIENTATION.

```html
<!DOCTYPE html>
<html lang="en">
<head>
<meta charset="utf-8">
<title>Brightfern Wellness – Business Card</title>
<link rel="stylesheet" href="https://fonts.googleapis.com/css2?family=Roboto+Condensed:wght@400;700&family=Roboto:wght@400&display=swap">
<style>
  :root {
    --stage: #e4e1dc;
    --card-dark: #121314;
    --brand-blue: #2a72b8;
    --brand-green: #0b6e35;
    --title-green: #167a3c;
    --ink-light: #ffffff;
    --band-text: #a9c9ea;
  }
  * { margin: 0; padding: 0; box-sizing: border-box; }
  html, body {
    width: 1200px; height: 960px; overflow: hidden;
    background: var(--stage);
  }
  .canvas { position: relative; width: 1200px; height: 960px; }

  .card {
    position: absolute;
    width: 600px; height: 343px;
    background: var(--card-dark);
    overflow: hidden;
  }
  .card--front { left: 314px; top: 113px; }
  .card--back  { left: 311px; top: 472px; }

  .front-shapes { position: absolute; inset: 0; }

  .identity { position: absolute; left: 34px; top: 31px; font-family: "Roboto Condensed", sans-serif; }
  .identity__name {
    color: var(--brand-blue); font-weight: 700; font-size: 19px;
    text-transform: uppercase; letter-spacing: 0.2px; line-height: 24px;
  }
  .identity__title { color: var(--title-green); font-size: 14px; line-height: 19px; }

  .brand-name {
    position: absolute; font-family: "Roboto Condensed", sans-serif;
    font-weight: 700; color: var(--brand-blue); white-space: nowrap;
  }
  .card--front .brand-name { left: 34px; top: 138px; font-size: 27px; }
  .card--back .brand-name {
    left: 0; right: 0; top: 118px; text-align: center; font-size: 46px;
  }

  .contact {
    position: absolute; right: 30px; top: 174px;
    font-family: "Roboto", sans-serif; font-size: 14px; color: var(--ink-light);
    text-align: right; line-height: 18px;
  }
  .contact__address { margin-bottom: 10px; }
  .contact__line { display: flex; justify-content: flex-end; align-items: center; gap: 4px; height: 19.5px; }
  .contact__icon { width: 12px; height: 12px; fill: var(--ink-light); flex: none; }

  .web-band {
    position: absolute; left: 0; right: 0; top: 278px; height: 31px;
    background: var(--brand-blue);
    font-family: "Roboto", sans-serif; font-size: 14px; letter-spacing: 4px;
    color: var(--band-text); text-align: center; line-height: 31px;
  }
</style>
</head>
<body>
<main class="canvas">

  <section class="card card--front">
    <svg class="front-shapes" width="600" height="343" viewBox="0 0 600 343">
      <path fill="var(--brand-blue)" d="M410,0 L600,0 L600,343 L125,343 C330,270 440,160 410,0 Z"/>
      <path fill="var(--brand-green)" stroke="#0a2a14" stroke-width="1" d="M372,0 C445,30 400,215 118,343 L125,343 C330,270 440,160 410,0 Z"/>
    </svg>

    <div class="identity">
      <p class="identity__name">Gerald M. Whitcombe, Ph.D.</p>
      <p class="identity__title">Licensed Clinical Psychologist</p>
      <p class="identity__title">Integrative Health Coach</p>
    </div>

    <p class="brand-name">Brightfern Wellness</p>

    <div class="contact">
      <div class="contact__address">
        <p>4812 Marlowe Ridge Blvd SE</p>
        <p>Suite 310</p>
        <p>Duluth, GA 30096</p>
      </div>
      <p class="contact__line">(770) 415-2983
        <svg class="contact__icon" viewBox="0 0 24 24"><path d="M6.6 10.8a15 15 0 0 0 6.6 6.6l2.2-2.2c.3-.3.7-.4 1-.2 1.1.4 2.3.6 3.6.6.6 0 1 .4 1 1V20c0 .6-.4 1-1 1C10.6 21 3 13.4 3 4c0-.6.4-1 1-1h3.5c.6 0 1 .4 1 1 0 1.3.2 2.5.6 3.6.1.3 0 .7-.2 1z"/></svg>
      </p>
      <p class="contact__line">(770) 581-4096
        <svg class="contact__icon" viewBox="0 0 24 24"><path d="M6 2h12v6H6zM3 9h18a1 1 0 0 1 1 1v7h-4v5H6v-5H2v-7a1 1 0 0 1 1-1zm5 8v3h8v-3z"/></svg>
      </p>
      <p class="contact__line">drgeraldwhitcombe@quillmarsh.net
        <svg class="contact__icon" viewBox="0 0 24 24"><path d="M2 5h20v14H2zm2 2v.5l8 5 8-5V7l-8 5z"/></svg>
      </p>
      <p class="contact__line">www.brightfernwellness.net
        <svg class="contact__icon" viewBox="0 0 24 24"><circle cx="12" cy="12" r="10"/><path fill="var(--brand-blue)" d="M7 7c2 0 3 1 3 3s-2 1-2 3 2 2 2 4c-2 0-4-2-4-5 0-2 0-4 1-5zm8-2c1 1 3 2 4 4-1 1-3 0-4 1s1 3-1 4-2-2-2-3 1-2 1-3-1-2 2-3z"/></svg>
      </p>
    </div>
  </section>

  <section class="card card--back">
    <p class="brand-name">Brightfern Wellness</p>
    <p class="web-band">www.brightfernwellness.net</p>
  </section>

</main>
</body>
</html>
```